Volbrey Inc Business Card

Looking to get an updated business card for a Contract Machining company (www.volbreyinc.example) - looking for a clean design the portrays the technical nature of the business - colors can follow the website design and be in any combination that makes sense (red black, white, metallic or silver) - logos attached for use also. Would like space for: Name, title, business phone (555 214-3086), cell phone , website (www.volbreyinc.example) - possibly QR code could be integrated for website (designer choice), business address - 418 Harlow Bend, Corrin Falls, NV 48199 (cards will be for 4 employees, I will either need to modify a template or I can provide individual information)
Target Market(s)
Aerospace, defense and medical device manufacturing companies that need machining
Industry/Entity Type
Machining for aerospace, defense, medical
Contact Information for Business Card
Name, Title, Business Phone, Cell Phone, email, business website and business address
Look and feel

```html
<!DOCTYPE html>
<html lang="en">
<head>
<meta charset="utf-8">
<title>Volbrey Inc Business Card</title>
<link href="https://fonts.googleapis.com/css2?family=Arimo:wght@400;700&display=swap" rel="stylesheet">
<style>
  :root {
    --backdrop: #3a3a3a;
    --card-dark: #2c2c2c;
    --card-light: #ffffff;
    --brand-red: #b11f24;
    --ink: #3b3b3b;
    --ink-soft: #7a7a7a;
    --rule: #cfcfcf;
    --watermark: #faf3f3;
  }
  * { box-sizing: border-box; margin: 0; padding: 0; }
  html, body { width: 1200px; height: 689px; overflow: hidden; }
  body {
    background: var(--backdrop);
    font-family: "Arimo", Arial, sans-serif;
    position: relative;
  }
  .card {
    position: absolute;
    top: 190px;
    width: 525px;
    height: 300px;
    border-radius: 14px;
    overflow: hidden;
  }
  .card--back { left: 45px; background: var(--card-dark); }
  .card--front { left: 630px; background: var(--card-light); }

  /* back */
  .back-mark {
    position: absolute; left: 50%; top: 50%;
    transform: translate(-50%, -50%);
    display: flex; flex-direction: column; align-items: center; gap: 14px;
  }
  .brand-disc { border-radius: 50%; background: var(--brand-red); }
  .back-mark .brand-disc { width: 130px; height: 130px; }
  .brand-name {
    color: var(--brand-red); font-weight: 700; letter-spacing: 2px;
    text-transform: uppercase; white-space: nowrap;
  }
  .back-mark .brand-name { font-size: 30px; }

  /* front */
  .watermark {
    position: absolute; left: 25px; top: 55px;
    width: 300px; height: 300px; border-radius: 50%;
    background: var(--watermark);
  }
  .front-mark {
    position: absolute; right: 38px; top: 26px;
    display: flex; flex-direction: column; align-items: center; gap: 8px;
  }
  .front-mark .brand-disc { width: 88px; height: 88px; }
  .front-mark .brand-name { font-size: 19px; }
  .top-rule {
    position: absolute; right: 28px; top: 152px;
    width: 330px; height: 1px; background: var(--rule);
  }
  .address {
    position: absolute; right: 30px; top: 166px;
    text-align: right; color: var(--ink); font-size: 13px; line-height: 1.35;
    font-style: normal;
  }
  .web-band {
    position: absolute; right: 0; bottom: 0;
    width: 195px; height: 34px; background: var(--brand-red);
    clip-path: polygon(4% 0, 100% 0, 100% 100%, 0 100%);
    color: #fff; font-size: 12.5px;
    display: flex; align-items: center; justify-content: flex-end; padding-right: 16px;
  }
  .person { position: absolute; left: 40px; top: 172px; }
  .person-name { color: var(--brand-red); font-weight: 700; font-size: 22px; }
  .person-title { color: var(--ink-soft); font-size: 13px; margin-top: 2px; }
  .person-rule { width: 200px; height: 1px; background: var(--rule); margin: 8px 0 6px; }
  .contact-list { list-style: none; color: var(--ink); font-size: 12.5px; line-height: 1.45; }
  .contact-list li { display: flex; align-items: center; gap: 7px; }
  .contact-list svg { width: 11px; height: 11px; fill: var(--brand-red); flex: none; }
</style>
</head>
<body>
  <section class="card card--back" aria-label="Card back">
    <div class="back-mark">
      <div class="brand-disc"></div>
      <div class="brand-name">Volbrey Inc.</div>
    </div>
  </section>

  <section class="card card--front" aria-label="Card front">
    <div class="watermark"></div>
    <div class="front-mark">
      <div class="brand-disc"></div>
      <div class="brand-name">Volbrey Inc.</div>
    </div>
    <div class="top-rule"></div>
    <address class="address">
      418 Harlow Bend<br>Corrin Falls, NV 48199
    </address>
    <div class="person">
      <div class="person-name">Dana Merrick</div>
      <div class="person-title">President</div>
      <div class="person-rule"></div>
      <ul class="contact-list">
        <li><svg viewBox="0 0 24 24"><path d="M6.6 10.8a15 15 0 0 0 6.6 6.6l2.2-2.2c.3-.3.7-.4 1-.2 1.1.4 2.3.6 3.6.6.6 0 1 .4 1 1V20c0 .6-.4 1-1 1A17 17 0 0 1 3 4c0-.6.4-1 1-1h3.5c.6 0 1 .4 1 1 0 1.3.2 2.5.6 3.6.1.3 0 .7-.2 1z"/></svg>555 214-3086</li>
        <li><svg viewBox="0 0 24 24"><path d="M7 1h10a2 2 0 0 1 2 2v18a2 2 0 0 1-2 2H7a2 2 0 0 1-2-2V3a2 2 0 0 1 2-2zm0 3v14h10V4z"/></svg>555 730-4412</li>
        <li><svg viewBox="0 0 24 24"><path d="M2 5h20v14H2zm2 2v.5l8 5 8-5V7z"/></svg>info@volbreyinc.example</li>
      </ul>
    </div>
    <div class="web-band">www.volbreyinc.example</div>
  </section>
</body>
</html>
```